Heron Haulage needs Bussiness cards!

Our new trucking company needs business cards!
We need the same design with two different names and emails, everything else it's the same.
I have included our original logo so we can use it for the design.
Note: the logo to be used is the o e with the buffalo on the right side, next to the letters H and H.

Target Market(s)

Trucking, refrigerated transportation, freight

Industry/Entity Type

Business

Contact Information for Business Card

Card #1:
Marcus Whitfield
marcuswhitfield@heronhaulage.example
1-855-317-6094
(956)238-7160
4117 W. Larkin Ave.
Pharr, TX 78590
www.heronhaulage.example

Card#2:
Rosalba Quintero
rosalba@heronhaulage.example
1-855-317-6094
(956)238-7160
4117 W. Larkin Ave.
Pharr, TX 78590
www.heronhaulage.example

Font styles to use
Sans Serif

Colors
0655a3
ec1f27
ffffff

Requirements
Must have
• our logo
Nice to have
• roads on background,

```html
<!DOCTYPE html>
<html lang="en">
<head>
<meta charset="utf-8">
<title>Heron Haulage — Business Cards</title>
<link href="https://fonts.googleapis.com/css2?family=Source+Sans+3:wght@400;600;700;800&display=swap" rel="stylesheet">
<style>
  :root {
    --stage: #151515;
    --card-white: #ffffff;
    --navy: #13294f;
    --deep-blue: #0b3364;
    --brand-red: #b5121b;
    --text-red: #c0141c;
    --icon-dark: #1b1b1b;
    --fade: #f6f7f9;
  }
  * { margin: 0; padding: 0; box-sizing: border-box; }
  html, body {
    width: 1200px; height: 900px; overflow: hidden;
    background: var(--stage);
    font-family: "Source Sans 3", "Segoe UI", sans-serif;
  }
  .card {
    position: absolute;
    width: 440px; height: 272px;
    border-radius: 11px;
    overflow: hidden;
  }
  .card--front { left: 149px; top: 305px; background: var(--card-white); }
  .card--back {
    left: 608px; top: 305px;
    background: linear-gradient(180deg, var(--deep-blue) 0%, #5c7593 38%, #b9c3cf 68%, var(--fade) 100%);
  }
  .wordmark {
    position: absolute;
    font-weight: 800;
    letter-spacing: -0.5px;
    white-space: nowrap;
    line-height: 1;
  }
  .card--front .wordmark {
    left: 0; right: 0; top: 52px;
    text-align: center;
    font-size: 38px;
    color: var(--navy);
    padding-left: 118px;
    text-align: left;
  }
  .card--back .wordmark {
    left: 0; right: 0; top: 112px;
    text-align: center;
    font-size: 46px;
    color: var(--brand-red);
  }
  .holder-name {
    position: absolute;
    left: 33px; top: 136px;
    font-size: 16px; font-weight: 600;
    color: var(--navy);
  }
  .contact-list {
    position: absolute;
    left: 34px; top: 177px;
    list-style: none;
  }
  .contact-list li {
    display: flex; align-items: center;
    height: 16.5px;
    font-size: 12.5px;
    color: var(--text-red);
  }
  .contact-list svg { width: 10px; height: 10px; margin-right: 5px; fill: var(--icon-dark); flex: none; }
  .address {
    position: absolute;
    right: 30px; top: 171px;
    text-align: right;
    font-size: 12.5px; line-height: 16.5px;
    color: var(--text-red);
  }
</style>
</head>
<body>
  <section class="card card--front" aria-label="Business card front">
    <div class="wordmark">Heron Haulage</div>
    <div class="holder-name">Marcus Whitfield</div>
    <ul class="contact-list">
      <li><svg viewBox="0 0 10 10"><rect x="2.5" y="0" width="5" height="10" rx="1"/><rect x="3.5" y="1.2" width="3" height="6" fill="#fff"/></svg>(956)238-7160</li>
      <li><svg viewBox="0 0 10 10"><rect x="2.5" y="0" width="5" height="10" rx="1"/><rect x="3.5" y="1.2" width="3" height="6" fill="#fff"/></svg>1-855-317-6094</li>
      <li><svg viewBox="0 0 10 10"><rect x="1" y="2" width="8" height="6"/><path d="M1 2 L5 5.5 L9 2" stroke="#fff" stroke-width="0.8" fill="none"/></svg>marcuswhitfield@heronhaulage.example</li>
      <li><svg viewBox="0 0 10 10"><circle cx="5" cy="5" r="4.5"/><path d="M0.5 5 H9.5 M5 0.5 C2.5 3 2.5 7 5 9.5 M5 0.5 C7.5 3 7.5 7 5 9.5" stroke="#fff" stroke-width="0.7" fill="none"/></svg>www.heronhaulage.example</li>
    </ul>
    <div class="address">4117 W. Larkin Ave.<br>Pharr, TX 78590</div>
  </section>

  <section class="card card--back" aria-label="Business card back">
    <div class="wordmark">Heron Haulage</div>
  </section>
</body>
</html>
```